Redesign of business card for Cedar Ridge Mechanical

We are looking for a new design for our business cards for Cedar Ridge Mechanical. We are a plumbing & HVAC construction company, operating on the West Coast of Canada and USA. Logo attached.
Industry/Entity Type
Construction - Plumbing & HVAC
Contact Information for Business Card
Name, address, phone numbers, email, website address
Look and feel
Each slider illustrates characteristics of the customer's brand and the style your logo design should communicate.

```html
<!DOCTYPE html>
<html lang="en">
<head>
<meta charset="utf-8">
<title>Cedar Ridge Mechanical – Business Card</title>
<link href="https://fonts.googleapis.com/css2?family=Open+Sans:wght@400;600;700&display=swap" rel="stylesheet">
<style>
  :root {
    --backdrop: #e6e1da;
    --card: #f2efea;
    --band-dark: #232120;
    --band-mid: #5e5954;
    --text-warm: #cdbba5;
    --text-muted: #bfae99;
    --logo-ink: #1d1b19;
  }
  html, body {
    margin: 0;
    padding: 0;
    width: 1200px;
    height: 1047px;
    overflow: hidden;
    background: var(--backdrop);
    font-family: "Open Sans", Arial, sans-serif;
  }
  .business-card {
    position: absolute;
    left: 100px;
    top: 238px;
    width: 1000px;
    height: 570px;
    border-radius: 26px;
    overflow: hidden;
    background: var(--card);
    box-shadow: 0 14px 40px rgba(0,0,0,0.18);
  }
  .card-swoosh {
    position: absolute;
    inset: 0;
    background: linear-gradient(to top right,
      var(--band-dark) 0%,
      var(--band-dark) 53%,
      var(--band-mid) 58%,
      var(--card) 65%,
      var(--card) 100%);
  }
  .brand-block {
    position: absolute;
    right: 60px;
    top: 58px;
    display: flex;
    align-items: center;
    gap: 18px;
  }
  .brand-mark {
    width: 44px;
    height: 44px;
    background: var(--logo-ink);
  }
  .brand-name {
    font-size: 34px;
    font-weight: 700;
    line-height: 1.15;
    letter-spacing: 1px;
    color: var(--logo-ink);
    text-transform: uppercase;
  }
  .contact-block {
    position: absolute;
    left: 46px;
    top: 178px;
    color: var(--text-warm);
  }
  .person-name {
    font-size: 30px;
    font-weight: 700;
    letter-spacing: 0.5px;
    margin: 0;
  }
  .person-role {
    font-size: 22px;
    margin: 4px 0 0;
    color: var(--text-muted);
  }
  .address {
    font-size: 22px;
    line-height: 38px;
    margin: 34px 0 0;
    color: var(--text-muted);
  }
  .contact-list {
    list-style: none;
    padding: 0;
    margin: 32px 0 0;
    font-size: 22px;
    line-height: 38px;
    color: var(--text-muted);
  }
  .contact-list li {
    display: flex;
    align-items: center;
    gap: 8px;
  }
  .contact-icon {
    width: 20px;
    height: 20px;
    fill: var(--text-muted);
  }
</style>
</head>
<body>
  <section class="business-card">
    <div class="card-swoosh" role="img" aria-label="Decorative dark wave swoosh across the card"></div>

    <div class="brand-block">
      <div class="brand-mark"></div>
      <div class="brand-name">Cedar Ridge<br>Mechanical</div>
    </div>

    <div class="contact-block">
      <h1 class="person-name">DANIEL HART</h1>
      <p class="person-role">Managing Director</p>
      <p class="address">Your address, City<br>State, Zip 1234</p>
      <ul class="contact-list">
        <li>
          <svg class="contact-icon" viewBox="0 0 24 24"><path d="M6.6 10.8a15 15 0 0 0 6.6 6.6l2.2-2.2a1 1 0 0 1 1-.25 11.4 11.4 0 0 0 3.6.57 1 1 0 0 1 1 1V20a1 1 0 0 1-1 1A17 17 0 0 1 3 4a1 1 0 0 1 1-1h3.5a1 1 0 0 1 1 1c0 1.25.2 2.45.57 3.57a1 1 0 0 1-.25 1z"/></svg>
          123 456 789
        </li>
        <li>
          <svg class="contact-icon" viewBox="0 0 24 24"><path d="M3 5h18a1 1 0 0 1 1 1v12a1 1 0 0 1-1 1H3a1 1 0 0 1-1-1V6a1 1 0 0 1 1-1zm1 2v.4l8 5 8-5V7l-8 5z"/></svg>
          info@yourmail.com
        </li>
        <li>
          <svg class="contact-icon" viewBox="0 0 24 24"><circle cx="12" cy="12" r="10"/></svg>
          www.yourwebsite.com
        </li>
      </ul>
    </div>
  </section>
</body>
</html>
```